Heron Loan Partners Business Card

We need a business card design for our mortgage servicing company. In addition to servicing the loans of homeowners, we help homeowners with purchasing their homes and any mortgage refinancing. We would like to see designs that use the colors in the logo attached below (gold-ish yellow and navy blue), and any other design you deem fit! The design should communicate a simpler life with smart mortgages provided by Heron.

```html
<!DOCTYPE html>
<html lang="en">
<head>
<meta charset="utf-8">
<title>Heron Loan Partners Business Card</title>
<link href="https://fonts.googleapis.com/css2?family=Open+Sans:wght@400;600;700&display=swap" rel="stylesheet">
<style>
  :root {
    --page: #d8cfc3;
    --card: #e9e2d7;
    --card-edge: #f4efe7;
    --gold: #c8921f;
    --gold-band: #d39a2a;
    --ink: #25262b;
    --ink-soft: #3a3b40;
    --band-text: #eedcb8;
  }
  * { box-sizing: border-box; margin: 0; padding: 0; }
  html, body {
    width: 1200px; height: 1046px; overflow: hidden;
    background: var(--page);
    font-family: "Open Sans", Arial, sans-serif;
  }
  .card {
    position: absolute; left: 100px; top: 250px;
    width: 1000px; height: 546px;
    background: var(--card);
    border: 1px solid var(--card-edge);
    box-shadow: 0 10px 30px rgba(60, 45, 25, 0.15);
  }
  .brand {
    position: absolute; left: 0; right: 0; top: 88px;
    text-align: center;
    font-size: 46px; font-weight: 700; color: var(--gold);
    letter-spacing: 0.5px;
  }
  .person {
    position: absolute; right: 551px; top: 318px;
    text-align: right;
  }
  .person-name {
    font-size: 41px; font-weight: 700; color: var(--ink);
    line-height: 1.1; letter-spacing: 0.5px;
  }
  .person-name .first { color: var(--gold); }
  .person-role {
    font-size: 26px; font-weight: 600; color: var(--ink-soft);
    margin-top: 2px; letter-spacing: 0.5px;
  }
  .divider {
    position: absolute; left: 499px; top: 302px;
    width: 1.5px; height: 154px; background: var(--ink);
  }
  .contacts {
    position: absolute; left: 575px; top: 326px;
    list-style: none;
  }
  .contact {
    display: flex; align-items: center; gap: 12px;
    height: 33px;
    font-size: 25px; color: var(--ink); letter-spacing: 0.5px;
  }
  .contact svg { width: 20px; height: 20px; flex: none; fill: var(--gold); }
  .address-band {
    position: absolute; left: 0; right: 0; top: 475px; height: 38px;
    background: var(--gold-band);
    display: flex; align-items: center; justify-content: center;
    font-size: 24px; color: var(--band-text); letter-spacing: 0.5px;
  }
</style>
</head>
<body>
  <div class="card">
    <div class="brand">Heron Loan Partners</div>

    <div class="person">
      <div class="person-name"><span class="first">Lena</span> Varga</div>
      <div class="person-role">Managing Director</div>
    </div>

    <div class="divider"></div>

    <ul class="contacts">
      <li class="contact">
        <svg viewBox="0 0 24 24" aria-hidden="true"><path d="M6.6 10.8c1.4 2.8 3.8 5.2 6.6 6.6l2.2-2.2c.3-.3.7-.4 1-.2 1.1.4 2.3.6 3.6.6.6 0 1 .4 1 1V20c0 .6-.4 1-1 1C10.6 21 3 13.4 3 4c0-.6.4-1 1-1h3.5c.6 0 1 .4 1 1 0 1.3.2 2.5.6 3.6.1.3 0 .7-.2 1L6.6 10.8z"/></svg>
        <span>(555) 204-3187</span>
      </li>
      <li class="contact">
        <svg viewBox="0 0 24 24" aria-hidden="true"><path d="M3 6h18v12H3z M3 6l9 7 9-7" fill="none" stroke="#c8921f" stroke-width="2"/></svg>
        <span>hello@heronloan.com</span>
      </li>
      <li class="contact">
        <svg viewBox="0 0 24 24" aria-hidden="true"><circle cx="12" cy="12" r="9" fill="none" stroke="#c8921f" stroke-width="2"/><path d="M3 12h18M12 3c3 3 3 15 0 18M12 3c-3 3-3 15 0 18" fill="none" stroke="#c8921f" stroke-width="1.6"/></svg>
        <span>www.heronloan.com</span>
      </li>
    </ul>

    <div class="address-band">2480 Tidewater Ln #204, Palm Bay, FL 32905, USA</div>
  </div>
</body>
</html>
```